Business Card for a Dental Office

The design should communicate integrity, quality and reliability. We also want the card look elegant, simple, but still stand out, different from the traditional-dental-office business card.

Industry/Entity Type

Business

```html
<!DOCTYPE html>
<html lang="en">
<head>
<meta charset="utf-8">
<title>Harbourline Dental Centre – Business Cards</title>
<link rel="stylesheet" href="https://fonts.googleapis.com/css2?family=Open+Sans:ital,wght@0,400;0,600;0,700;1,600&display=swap">
<style>
  :root {
    --backdrop: #2a2c30;
    --card: #ffffff;
    --ink: #111111;
    --ink-soft: #2b2b2b;
    --gold: #c9a514;
    --gold-deep: #a88a0c;
    --rule: #b9b9b9;
    --dots: #333333;
  }
  * { box-sizing: border-box; margin: 0; padding: 0; }
  html, body {
    width: 1200px; height: 864px; overflow: hidden;
    background: var(--backdrop);
    font-family: "Open Sans", Arial, sans-serif;
  }
  .card {
    position: absolute;
    width: 560px; height: 320px;
    background: var(--card);
    color: var(--ink);
  }
  .card--appointment { left: 150px; top: 62px; }
  .card--contact { left: 490px; top: 482px; }

  .brand { text-align: center; }
  .brand__name {
    font-weight: 700; font-size: 27px; letter-spacing: 0.5px;
    text-transform: uppercase; color: var(--ink); line-height: 1;
  }
  .brand__tagline {
    font-weight: 600; font-size: 11.5px; letter-spacing: 1.6px;
    text-transform: uppercase; color: var(--gold); margin-top: 3px;
  }

  .card--appointment .brand { padding-top: 34px; }
  .appointment__title {
    text-align: center; color: var(--gold); font-weight: 600;
    font-size: 19px; margin-top: 16px;
  }
  .appointment__fields { margin: 14px 0 0 92px; width: 390px; }
  .field {
    display: flex; align-items: flex-end; gap: 6px;
    font-size: 12.5px; font-weight: 700; color: var(--ink-soft);
    height: 28px;
  }
  .field__line {
    flex: 1; border-bottom: 2px dotted var(--dots); margin-bottom: 4px;
  }
  .appointment__notice {
    text-align: center; color: var(--gold); font-style: italic;
    font-weight: 600; font-size: 13.5px; margin-top: 14px;
  }

  .card--contact .brand {
    position: absolute; right: 46px; top: 54px;
    display: flex; align-items: center; gap: 12px; text-align: left;
  }
  .brand__mark { width: 34px; height: 34px; background: var(--gold); flex: none; }
  .person { position: absolute; left: 40px; top: 130px; }
  .person__name { color: var(--gold); font-size: 21px; font-weight: 600; line-height: 1.1; }
  .person__role { font-size: 13px; color: var(--ink-soft); }
  .divider {
    position: absolute; left: 200px; right: 46px; top: 160px;
    border-top: 1px solid var(--rule);
  }
  .contacts {
    position: absolute; right: 46px; top: 196px; list-style: none;
    text-align: right; font-size: 14px; color: var(--ink);
  }
  .contacts li {
    display: flex; justify-content: flex-end; align-items: center;
    gap: 10px; height: 21px;
  }
  .contacts svg { width: 12px; height: 12px; fill: var(--gold); flex: none; }
</style>
</head>
<body>

<section class="card card--appointment">
  <div class="brand">
    <p class="brand__name">Harbourline Dental Centre</p>
    <p class="brand__tagline">Your smile is your gift to others</p>
  </div>
  <h2 class="appointment__title">Your Next Appointment is</h2>
  <div class="appointment__fields">
    <div class="field"><span>Name :</span><span class="field__line"></span></div>
    <div class="field"><span>Date :</span><span class="field__line"></span></div>
    <div class="field"><span>Time :</span><span class="field__line"></span><span>AM</span><span class="field__line"></span><span>PM</span></div>
  </div>
  <p class="appointment__notice">If unable to keep appointment, kindly give 24hrs notice.</p>
</section>

<section class="card card--contact">
  <div class="brand">
    <span class="brand__mark"></span>
    <div>
      <p class="brand__name">Harbourline Dental Centre</p>
      <p class="brand__tagline">Your smile is your gift to others</p>
    </div>
  </div>
  <div class="person">
    <p class="person__name">Daniel Reyes</p>
    <p class="person__role">Managing Director</p>
  </div>
  <div class="divider"></div>
  <ul class="contacts">
    <li>044-555-0148
      <svg viewBox="0 0 24 24" aria-hidden="true"><path d="M6.6 10.8a15 15 0 0 0 6.6 6.6l2.2-2.2c.3-.3.7-.4 1-.2 1.1.4 2.3.6 3.6.6.6 0 1 .4 1 1V20c0 .6-.4 1-1 1A17 17 0 0 1 3 4c0-.6.4-1 1-1h3.5c.6 0 1 .4 1 1 0 1.3.2 2.5.6 3.6.1.3 0 .7-.2 1z"/></svg></li>
    <li>123-555-0162
      <svg viewBox="0 0 24 24" aria-hidden="true"><path d="M6 2h10v6H6zM3 9h18v11H3zm3 3v2h4v-2zm0 4v2h4v-2zm8-4v6h4v-6z"/></svg></li>
    <li>123-555-0179
      <svg viewBox="0 0 24 24" aria-hidden="true"><path d="M7 1h10a2 2 0 0 1 2 2v18a2 2 0 0 1-2 2H7a2 2 0 0 1-2-2V3a2 2 0 0 1 2-2zm0 3v14h10V4zm5 15.5a1.2 1.2 0 1 0 0 2.4 1.2 1.2 0 0 0 0-2.4z"/></svg></li>
    <li>hello@harbourlinedental.com
      <svg viewBox="0 0 24 24" aria-hidden="true"><path d="M2 5h20v14H2zm2 2v.5l8 5 8-5V7z"/></svg></li>
    <li>www.harbourlinedental.com
      <svg viewBox="0 0 24 24" aria-hidden="true"><path d="M10.6 13.4a1 1 0 0 1 0-1.4l3.5-3.5a1 1 0 1 1 1.4 1.4L12 13.4a1 1 0 0 1-1.4 0zM8 11l-3 3a3.5 3.5 0 0 0 5 5l3-3-1.4-1.4-3 3a1.5 1.5 0 0 1-2.2-2.2l3-3zm8 2 3-3a3.5 3.5 0 0 0-5-5l-3 3 1.4 1.4 3-3a1.5 1.5 0 0 1 2.2 2.2l-3 3z"/></svg></li>
  </ul>
</section>

</body>
</html>
```